Hearthside Lending Relief

Please help us give our website a remake or a FACELIFT. It is not very good but it says what we need it to say. But the design is terrible.
I would like our new design font and logo to be used as the theme.

I also want more photos on the site.

I also want consistency with the pages so they look clean.

We want the professionals to do this, let's see what you got!

Thank you!
Updates

Project Deadline Extended
Reason: I can understand you want to be paid. So I will commit to the fee but I want you to have time to make a KICK ASS website for me dudes! Thanks

HI!  Just wanted to say thanks for your time on these.  A lot are great.  However the firefighters have nothing to do with Foreclosure.  We are saving peoples homes from the bank taking them and selling them.   I LOVE the house photos and the families on the website.  That is the direction we like.  THanks.

THANK U ALL FOR THE WORK!   I like a few ending in the numbers: 147  733  693  536  620  478  727  508     I will go over them and choose one soon.  Thank you.   You will be paid shortly. 

Requirements
Must have
• Bright, Upbeat photos. Color scheme should be in order. We like icons on the bottom. not just text.

```html
<!DOCTYPE html>
<html lang="en">
<head>
<meta charset="utf-8">
<title>Hearthside Lending Relief</title>
<link href="https://fonts.googleapis.com/css2?family=Arimo:ital,wght@0,400;0,700;1,400&family=Cinzel:wght@700&display=swap" rel="stylesheet">
<style>
:root{
  --red:#d8281f;
  --red-dark:#b51d16;
  --ink:#3a3a3a;
  --muted:#7a7a7a;
  --line:#d9d9d9;
  --nav:#2d2d2d;
  --page:#ececec;
  --panel:#ffffff;
  --footer:#13294a;
  --footer-deep:#0c1c35;
  --sky:#9cc3e4;
  --lawn:#7fa456;
}
*{box-sizing:border-box;margin:0;padding:0}
html,body{width:816px;height:1200px;overflow:hidden}
body{background:var(--page);font-family:"Arimo",Arial,sans-serif;color:var(--ink);font-size:9px;position:relative}
.abs{position:absolute}
.utility{top:4px;right:103px;display:flex;gap:3px}
.utility span{background:#fff;border:1px solid var(--line);font-size:7px;padding:2px 6px;color:var(--muted)}
.brand{left:103px;top:34px;display:flex;align-items:center;gap:10px}
.brand-mark{width:50px;height:50px;border-radius:50%;background:var(--red)}
.brand-name{font-weight:700;font-size:19px;line-height:1.05;color:var(--red);text-transform:uppercase;width:190px}
.tollfree{right:103px;top:56px;font-size:10px;color:var(--muted)}
.tollfree b{color:var(--red);font-size:22px;font-weight:400;margin-left:4px}
.nav{left:103px;top:103px;width:610px;height:30px;background:var(--nav);display:flex;align-items:center;padding:0 8px;gap:4px}
.nav a{color:#fff;font-size:8px;font-weight:700;text-decoration:none;padding:0 14px;letter-spacing:.3px}
.nav a.active{background:var(--red);line-height:30px}
.nav .search{margin-left:auto;display:flex}
.nav .search span{background:#fff;width:96px;height:16px;font-size:7px;color:#999;padding:3px 5px}
.nav .search i{width:16px;height:16px;background:var(--red)}
.hero{left:103px;top:141px;width:610px;height:267px;background:linear-gradient(180deg,var(--sky) 0%,#d9cfbf 45%,#c1a98a 70%,var(--lawn) 100%)}
.consult{left:511px;top:141px;width:202px;height:267px;background:rgba(216,40,31,.92);padding:0 10px;color:#fff}
.consult h3{background:var(--red-dark);margin:0 -10px 8px;padding:9px 10px;font-size:10px;text-align:center}
.consult p{font-size:8px;line-height:1.35;margin-bottom:8px}
.consult .field{background:#fff;height:19px;margin-bottom:7px;color:#999;font-size:7.5px;padding:5px 6px}
.consult .send{margin-top:10px;border:1px solid #fff;text-align:center;font-family:"Cinzel",serif;font-size:10px;padding:5px}
.thumbs{left:103px;top:430px;width:420px;display:flex;gap:12px}
.card{width:132px}
.thumb{height:84px;background:linear-gradient(160deg,var(--sky),#e4d6c3 60%,var(--lawn))}
.card p{font-size:7.5px;line-height:1.45;color:var(--muted);margin:9px 0 12px;height:46px}
.btn{display:inline-block;background:var(--red);color:#fff;font-size:8px;font-weight:700;padding:6px 12px}
.news{left:544px;top:422px;width:169px}
.cinzel{font-family:"Cinzel",serif;color:var(--red);font-weight:700}
.news h2{font-size:14px;padding-bottom:5px;border-bottom:2px solid var(--red);margin-bottom:6px}
.news li{list-style:none;font-size:7.2px;color:var(--muted);padding:3px 0 3px 11px;border-bottom:1px dotted var(--line);position:relative}
.news li::before{content:"";position:absolute;left:1px;top:6px;width:5px;height:5px;background:var(--red)}
.news .btn{display:block;width:78px;text-align:center;margin:10px auto 0}
.about{left:103px;top:665px;width:420px}
.about h2{font-size:15px;margin-bottom:5px}
.about p{font-size:9px;line-height:1.5;color:var(--muted);margin-bottom:10px}
.btn-light{display:inline-block;border:1px solid #bbb;background:#f4f4f4;font-size:8px;padding:5px 10px}
.contact{left:544px;top:653px;width:169px;height:272px;background:#f3f3f3;border:1px solid var(--line);padding:10px}
.contact h2{font-size:14px;text-align:center;color:#555;border-bottom:1px solid var(--line);padding-bottom:6px;margin-bottom:12px}
.row{display:flex;align-items:flex-start;gap:6px;margin-bottom:8px;font-size:7.5px;color:var(--muted)}
.row label{width:34px;padding-top:4px}
.row span{flex:1;height:18px;background:#fff;border:1px solid var(--line)}
.row span.tall{height:70px}
.contact .btn-light{float:right;margin-top:2px}
.testimonial{left:103px;top:828px;width:420px;text-align:center}
.testimonial h2{font-size:17px;margin-bottom:6px}
.quote{display:flex;gap:8px;align-items:flex-start;text-align:left}
.quote b{font-family:"Cinzel",serif;font-size:30px;color:#999;line-height:.8}
.quote p{font-style:italic;font-size:9px;line-height:1.5;color:var(--muted)}
.quote small{display:block;font-size:7px;margin-top:5px}
.footer{left:0;top:980px;width:816px;height:182px;background:var(--footer);color:#fff}
.fcol{position:absolute;top:24px}
.fcol h4{font-size:11px;margin-bottom:6px}
.fcol li{list-style:none;font-size:7.5px;color:#b9c6da;line-height:1.55}
.newsletter{position:absolute;left:380px;top:24px}
.newsletter h4{font-size:12px;margin-bottom:10px}
.nl-row{display:flex;gap:6px;align-items:center}
.nl-row span{width:140px;height:18px;background:#fff;color:#999;font-size:7px;padding:4px 6px}
.nl-row em{background:var(--red);font-style:normal;font-size:8px;padding:4px 8px}
.nl-row i{width:18px;height:18px;background:#fff;border-radius:3px;margin-left:4px}
.bottom{left:0;top:1162px;width:816px;height:38px;background:var(--footer-deep);color:#9fb0c9;font-size:7px;padding:8px 103px;line-height:1.6}
</style>
</head>
<body>
<div class="abs utility"><span>Login</span><span>Contact</span></div>

<div class="abs brand"><div class="brand-mark"></div><div class="brand-name">Hearthside Lending Relief</div></div>
<div class="abs tollfree">Call Toll-Free Now<b>877-555-0142</b></div>

<nav class="abs nav">
  <svg width="16" height="14" viewBox="0 0 16 14"><path d="M8 1 1 7h2v6h4V9h2v4h4V7h2z" fill="#fff"/></svg>
  <a class="active">ABOUT US</a><a>SERVICES</a><a>FINANCING OPTIONS</a><a>CONTACT US</a>
  <div class="search"><span>Search</span><i></i></div>
</nav>

<div class="abs hero" role="img" aria-label="Smiling family standing in front of their suburban home"></div>
<form class="abs consult">
  <h3>GET A FREE CONSULTATION</h3>
  <p>Please fill out this form, and we'll call you as soon as possible.</p>
  <div class="field">Name *</div>
  <div class="field">Email *</div>
  <div class="field">Phone *</div>
  <div class="field">State property is ▾</div>
  <div class="send">SEND REQUEST</div>
</form>

<div class="abs thumbs">
  <div class="card"><div class="thumb" role="img" aria-label="Happy family outside a house"></div><p>We help owners keep their homes with clear options, honest advice and a plan that fits real budgets.</p><span class="btn">LEARN MORE</span></div>
  <div class="card"><div class="thumb" role="img" aria-label="Parents and child relaxing on a sunny lawn"></div><p>We help owners keep their homes with clear options, honest advice and a plan that fits real budgets.</p><span class="btn">LEARN MORE</span></div>
  <div class="card"><div class="thumb" role="img" aria-label="Bright family home with a green yard"></div><p>We help owners keep their homes with clear options, honest advice and a plan that fits real budgets.</p><span class="btn">LEARN MORE</span></div>
</div>

<aside class="abs news">
  <h2 class="cinzel">LATEST NEWS</h2>
  <ul>
    <li>New loan relief options announced</li>
    <li>How to talk with your lender</li>
    <li>Steps to pause a foreclosure</li>
    <li>Family keeps home after review</li>
    <li>Understanding loan modification</li>
    <li>Spring workshop dates posted</li>
    <li>Rate changes and your payment</li>
    <li>Planning a budget that works</li>
    <li>Questions owners often ask</li>
  </ul>
  <span class="btn">See More</span>
</aside>

<section class="abs about">
  <h2 class="cinzel">ABOUT HEARTHSIDE LENDING RELIEF</h2>
  <p>We stand with homeowners facing hard times. Our team reviews every loan with care, explains each option in plain words and works with lenders to find a path that keeps families in the homes they love. Call today and take the first step toward a calmer, more secure future.</p>
  <span class="btn-light">Read More</span>
</section>

<section class="abs contact">
  <h2 class="cinzel">CONTACT US</h2>
  <div class="row"><label>Name *</label><span></span></div>
  <div class="row"><label>Email *</label><span></span></div>
  <div class="row"><label>Message *</label><span class="tall"></span></div>
  <span class="btn-light">SEND</span>
</section>

<section class="abs testimonial">
  <h2 class="cinzel">TESTIMONIAL</h2>
  <div class="quote"><b>“</b><p>They listened, explained every step and helped us keep our home when we thought it was gone. We are grateful for their patience and care.<small>— Dana Whitfield, Home Owner</small></p><b>”</b></div>
</section>

<footer class="abs footer">
  <div class="fcol" style="left:103px"><h4>About Us</h4><ul><li>Our Company</li><li>Our Team</li><li>Clients</li><li>Partners</li></ul></div>
  <div class="fcol" style="left:190px"><h4>Advice</h4><ul><li>Start here</li><li>Process</li><li>Guides</li><li>Careers</li></ul></div>
  <div class="fcol" style="left:275px"><h4>Join In</h4><ul><li>Events</li><li>Forums</li><li>Support</li><li>Contact</li></ul></div>
  <div class="newsletter"><h4>Join our Newsletter</h4><div class="nl-row"><span>Email address</span><em>Subscribe</em><i></i><i></i><i></i></div></div>
</footer>
<div class="abs bottom">Disclaimer &amp; Terms &amp; Conditions | Privacy Policy | Advertise With Us | Contact Us<br>© Hearthside Lending Relief. All rights reserved.</div>
</body>
</html>
```